BildeVOLD buisnesscard

Hey :) I need a modern buisnesscard for my company BildeVOLD
It most have:
Dagligleder og Fotograf: Henrik Audun Strandvik

Mob: +4791264085
Epost: post@bildevold.example
Adresse: Kvernbakken9, 6040 Strandøy

Facbook and instagram logo with text BildeVOLD

BildeVOLD logo

It Company

```html
<!DOCTYPE html>
<html lang="no">
<head>
<meta charset="utf-8">
<title>BildeVOLD – visittkort</title>
<link rel="stylesheet" href="https://fonts.googleapis.com/css2?family=Open+Sans:wght@400;600;700&display=swap">
<style>
  :root {
    --backdrop: #e9e6e2;
    --card-black: #000000;
    --band-dark: #3b3b3b;
    --panel-grey: #b4b4b4;
    --mark-silver: #c2c2c2;
    --ink: #1c1c1c;
    --ink-strong: #111111;
  }
  * { box-sizing: border-box; margin: 0; padding: 0; }
  html, body {
    width: 1200px; height: 900px; overflow: hidden;
    background: var(--backdrop);
    font-family: "Open Sans", Arial, sans-serif;
  }
  .canvas { position: relative; width: 1200px; height: 900px; }

  .card { position: absolute; overflow: hidden; box-shadow: 0 6px 18px rgba(0,0,0,.18); }

  /* Front side */
  .card--front { left: 78px; top: 35px; width: 588px; height: 362px; background: var(--panel-grey); }
  .card__bands { position: absolute; inset: 0; }
  .card__wordmark {
    position: absolute; left: 0; right: 0; top: 66px;
    text-align: center; font-weight: 700; font-size: 66px; letter-spacing: 1px;
    color: var(--mark-silver); line-height: 1;
  }
  .contact { position: absolute; left: 30px; top: 266px; color: var(--ink); font-size: 15px; line-height: 21px; }
  .contact__row { display: flex; align-items: center; gap: 7px; }
  .contact__icon { width: 11px; height: 11px; flex: none; }
  .contact__address { margin-top: 4px; }

  .owner { position: absolute; right: 36px; top: 260px; text-align: right; color: var(--ink); }
  .owner__name { font-weight: 600; font-size: 17px; color: var(--ink-strong); margin-bottom: 10px; }
  .owner__social { display: flex; justify-content: flex-end; align-items: center; gap: 9px; font-size: 14px; line-height: 23px; }
  .owner__dot { width: 12px; height: 12px; background: var(--ink); flex: none; }

  /* Back side */
  .card--back { left: 388px; top: 505px; width: 566px; height: 352px; background: var(--card-black); }
  .back__square {
    position: absolute; left: 223px; top: 86px; width: 120px; height: 120px;
    background: var(--mark-silver);
  }
  .back__wordmark {
    position: absolute; left: 0; right: 0; top: 214px;
    text-align: center; font-weight: 700; font-size: 60px; letter-spacing: 1px;
    color: var(--mark-silver); line-height: 1;
  }
</style>
</head>
<body>
<main class="canvas">

  <section class="card card--front" aria-label="Visittkort forside">
    <svg class="card__bands" width="588" height="362" viewBox="0 0 588 362" aria-hidden="true">
      <rect x="0" y="0" width="588" height="190" fill="var(--card-black)"/>
      <polygon points="0,190 588,190 588,192 416,192 384,226 0,226" fill="var(--card-black)"/>
      <polygon points="0,198 412,198 384,226 0,226" fill="var(--band-dark)"/>
    </svg>

    <div class="card__wordmark">BildeVOLD</div>

    <div class="contact">
      <div class="contact__row">
        <svg class="contact__icon" viewBox="0 0 24 24" aria-hidden="true"><path fill="currentColor" d="M6.6 10.8a15.1 15.1 0 0 0 6.6 6.6l2.2-2.2c.3-.3.7-.4 1-.2 1.1.4 2.3.6 3.6.6.6 0 1 .4 1 1V20c0 .6-.4 1-1 1A17 17 0 0 1 3 4c0-.6.4-1 1-1h3.5c.6 0 1 .4 1 1 0 1.3.2 2.5.6 3.6.1.3 0 .7-.2 1z"/></svg>
        <span>+4791264085</span>
      </div>
      <div class="contact__row">
        <svg class="contact__icon" viewBox="0 0 24 24" aria-hidden="true"><path fill="currentColor" d="M2 5h20v14H2z M2 5l10 7 10-7" stroke="var(--panel-grey)" stroke-width="1.6"/></svg>
        <span>post@bildevold.example</span>
      </div>
      <div class="contact__address">Kvernbakken9, 6040 Strandøy</div>
    </div>

    <div class="owner">
      <div class="owner__name">Henrik Audun Strandvik</div>
      <div class="owner__social"><span>BildeVOLD</span><span class="owner__dot"></span></div>
      <div class="owner__social"><span>BildeVOLD</span><span class="owner__dot"></span></div>
    </div>
  </section>

  <section class="card card--back" aria-label="Visittkort bakside">
    <div class="back__square"></div>
    <div class="back__wordmark">BildeVOLD</div>
  </section>

</main>
</body>
</html>
```